New Dental Office Needs an Attractive and user friendly Website Designed

I need a website for a new dental office. The Name is Harrowfield Dentistry. I would like a Modern design with a user friendly interface and usability.
I would like a landing page, a page that lists the services we offer: Cosmetic Dentistry, Implants, Dental Hygiene, Emergency Services, Restorations, Dentures
Target Market(s)
Mid to upper class
Industry/Entity Type
Dentistry
Coding
Number of Pages Required
1 page
Requirements
Must have
- Landing page that has a scheduling option, Procedures, operating hours, and contact us info
Nice to have
- Appealing design, Soft comforting colors. Easy to navigate page, Modern and professional.

```html
<!DOCTYPE html>
<html lang="en">
<head>
<meta charset="utf-8">
<title>Harrowfield Dentistry</title>
<link href="https://fonts.googleapis.com/css2?family=Inter:wght@400;500;600;700&family=Playfair+Display:wght@400;700&display=swap" rel="stylesheet">
<style>
:root{
  --teal:#4aa39b;
  --teal-dark:#3d8f87;
  --green:#2f6e57;
  --ink:#2b2b2b;
  --muted:#555;
  --paper:#f7f7f5;
  --mint:#d8ebe8;
  --white:#ffffff;
  --line:#9fd0ca;
  --star:#f0b64a;
}
*{box-sizing:border-box;margin:0;padding:0}
html,body{width:1200px;height:4494px;overflow:hidden}
body{font-family:"Inter",sans-serif;color:var(--ink);background:var(--paper);position:relative}
section,header,footer,.topbar{position:relative;width:1200px}
.btn{position:absolute;display:flex;align-items:center;justify-content:center;background:var(--teal);color:var(--white);border-radius:8px;font-size:20px;font-weight:500}
.brand{font-family:"Inter",sans-serif;font-weight:600;color:var(--green);font-size:30px;letter-spacing:-.3px;display:flex;align-items:center;gap:10px}
.brand .dot{width:14px;height:14px;background:var(--teal);border-radius:50%}

.topbar{height:38px;background:var(--teal);color:var(--white);font-size:15px}
.topbar .item{position:absolute;top:10px;display:flex;align-items:center;gap:6px}

.nav{height:98px;background:var(--paper);border-bottom:1px solid var(--line)}
.nav .brand{position:absolute;left:96px;top:32px}
.nav .link{position:absolute;top:37px;font-size:18px;color:var(--ink)}

.hero{height:537px;background:linear-gradient(90deg,#fbfbfa 0%,#f5f3f1 45%,#efe6df 100%)}
.hero .photo{position:absolute;left:560px;top:0;width:640px;height:537px;background:linear-gradient(110deg,#f3ede8 0%,#d9b9a1 40%,#b9835f 65%,#e6ddd5 100%)}
.hero h1{position:absolute;left:87px;top:96px;font-family:"Playfair Display",serif;font-weight:700;font-size:60px;line-height:69px;color:var(--green)}
.hero p{position:absolute;left:87px;top:254px;font-size:27px;line-height:43px;color:#333}

.services{height:1115px;background:var(--paper)}
.section-title{position:absolute;left:0;width:1200px;text-align:center;font-family:"Playfair Display",serif;font-weight:400;font-size:48px;color:var(--green)}
.services .sub{position:absolute;top:173px;width:1200px;text-align:center;font-size:24px}
.card{position:absolute;width:328px;height:327px;background:var(--white);border:1.5px solid var(--line);border-radius:12px;text-align:center}
.card svg{position:absolute;left:129px;top:36px}
.card h3{position:absolute;top:132px;width:100%;font-size:25px;font-weight:600;color:var(--green)}
.card p{position:absolute;top:172px;width:100%;font-size:15.5px;line-height:24px;color:var(--muted)}
.card .btn{left:84px;top:246px;width:160px;height:49px}

.cta{height:232px;background:var(--teal)}
.cta h2{position:absolute;left:87px;top:92px;font-size:42px;font-weight:700;color:var(--white)}
.cta .outline{position:absolute;left:821px;top:90px;width:292px;height:53px;border:1.5px solid var(--white);background:var(--paper);color:#3a3a3a;border-radius:8px;display:flex;align-items:center;justify-content:center;font-size:20px}

.hours{height:640px;background:var(--paper)}
.hours .photo{position:absolute;left:0;top:0;width:577px;height:640px;background:linear-gradient(120deg,#8fb6b4 0%,#c99a7a 45%,#e8ddd4 70%,#3f8f96 100%)}
.hours h2{position:absolute;left:633px;font-family:"Playfair Display",serif;font-weight:400;font-size:46px;color:var(--green)}
.hours .row{position:absolute;left:633px;font-size:25px;color:#333}
.hours .row span{position:absolute;left:258px;white-space:nowrap}
.hours .addr{position:absolute;left:633px;top:402px;font-size:25px;line-height:32px;color:#333}

.reviews{height:549px;background:var(--mint)}
.review{position:absolute;top:195px;width:286px;height:246px;background:var(--white);border:1.5px solid var(--line);text-align:center}
.review .stars{position:absolute;top:32px;width:100%;color:var(--star);font-size:18px;letter-spacing:6px}
.review p{position:absolute;top:72px;width:100%;font-size:18.5px;line-height:31px;color:#444}
.review .name{position:absolute;top:184px;width:100%;font-size:18.5px;font-weight:600;color:#333}

.book{height:553px;background:var(--paper)}
.book .photo{position:absolute;left:631px;top:0;width:569px;height:553px;background:linear-gradient(115deg,#b7bfae 0%,#8a6249 35%,#d8b9a5 60%,#c6cbbf 100%)}
.book h2{position:absolute;left:87px;top:92px;font-family:"Playfair Display",serif;font-weight:400;font-size:46px;color:var(--green)}
.book p{position:absolute;left:91px;top:180px;font-size:24.5px;line-height:34.5px;color:#333;white-space:nowrap}

.news{height:310px;background:var(--mint)}
.news h2{position:absolute;left:87px;top:78px;font-size:45px;font-weight:700;color:var(--green)}
.news p{position:absolute;left:87px;top:160px;font-size:24px;line-height:35px;color:#333}
.news .field{position:absolute;left:682px;top:169px;width:429px;height:49px;background:var(--white);border:1.5px solid var(--line);border-radius:25px;font-size:15px;color:#444;padding:15px 0 0 26px}
.news .btn{left:950px;top:169px;width:161px;height:49px;border-radius:25px;font-size:22px}

.site-footer{height:297px;background:var(--paper);border-bottom:1.5px solid #cfdedb}
.site-footer .brand{position:absolute;left:87px;top:68px}
.site-footer .social{position:absolute;left:142px;top:159px;display:flex;gap:16px}
.site-footer .social span{width:26px;height:26px;border-radius:6px;background:var(--green)}
.site-footer .col{position:absolute;top:68px;font-size:18px;line-height:34px;color:#333}
.site-footer .col h4{font-size:24px;font-weight:600;color:var(--green);margin-bottom:12px;line-height:30px}
.site-footer .legal{position:absolute;left:104px;top:214px;font-size:18px;color:#333}
.copy{height:125px;text-align:center;font-size:18px;color:#333;padding-top:52px;background:var(--paper)}
</style>
</head>
<body>

<div class="topbar">
  <div class="item" style="left:93px">
    <svg width="12" height="16" viewBox="0 0 12 16"><path d="M6 0a6 6 0 0 0-6 6c0 4.5 6 10 6 10s6-5.5 6-10a6 6 0 0 0-6-6zm0 8.5A2.5 2.5 0 1 1 6 3.5a2.5 2.5 0 0 1 0 5z" fill="#fff"/></svg>
    48 Alder Lane, Brookvale, IL
  </div>
  <div class="item" style="left:965px">
    <svg width="10" height="16" viewBox="0 0 10 16"><rect x="0.5" y="0.5" width="9" height="15" rx="2" fill="#fff"/></svg>
    (555) 284-9106
  </div>
</div>

<header class="nav">
  <div class="brand"><span class="dot"></span>Harrowfield Dentistry</div>
  <a class="link" style="left:551px">Services</a>
  <a class="link" style="left:685px">About</a>
  <a class="link" style="left:794px">Contact</a>
  <div class="btn" style="left:947px;top:25px;width:166px;height:49px;font-size:21px">Book Online</div>
</header>

<section class="hero">
  <div class="photo" role="img" aria-label="Photo of a smiling patient in a knit sweater"></div>
  <h1>Exceptional Care<br>For Your Smile</h1>
  <p>Advanced Care with a Gentle Touch.<br>Because Your Smile Deserves the Best.</p>
  <div class="btn" style="left:87px;top:361px;width:272px;height:49px;font-size:20px">Schedule Appointment</div>
</section>

<section class="services">
  <h2 class="section-title" style="top:99px">Our Services</h2>
  <div class="sub">Comprehensive Dental Solutions, Tailored to You.</div>

  <div class="card" style="left:87px;top:264px">
    <svg width="70" height="76" viewBox="0 0 70 76" fill="none" stroke="#2f6e57" stroke-width="3" stroke-linecap="round" stroke-linejoin="round"><path d="M20 8c-10 0-16 8-14 20 2 10 6 14 7 26 1 10 4 16 8 16 5 0 5-14 9-20 4 6 4 20 9 20 4 0 7-6 8-16 1-12 5-16 6-24"/><path d="M24 10c6 2 10 2 14 0"/><path d="M56 6v14M49 13h14"/></svg>
    <h3>Cosmetic Dentistry</h3>
    <p>Whitening, veneers, and smile<br>makeovers for a confident appearance.</p>
    <div class="btn">Learn More</div>
  </div>
  <div class="card" style="left:436px;top:264px">
    <svg width="70" height="76" viewBox="0 0 70 76" fill="none" stroke="#2f6e57" stroke-width="3" stroke-linecap="round" stroke-linejoin="round"><path d="M14 10c0-6 6-8 12-6 6 2 12 2 18 0 6-2 12 0 12 6 0 8-4 12-6 14H20c-2-2-6-6-6-14z"/><path d="M22 24v6h26v-6"/><path d="M25 36h20M27 44h16M29 52h12M31 60h8M35 66v6"/></svg>
    <h3>Dental Implants</h3>
    <p>Permanent tooth replacement<br>with natural look, feel, and function.</p>
    <div class="btn">Learn More</div>
  </div>
  <div class="card" style="left:785px;top:264px">
    <svg width="80" height="76" viewBox="0 0 80 76" fill="none" stroke="#2f6e57" stroke-width="3" stroke-linecap="round" stroke-linejoin="round"><path d="M4 72l34-34"/><path d="M34 34l10 10"/><path d="M38 30l14-14 10 10-14 14z"/><path d="M42 26l4 4M46 22l4 4M50 18l4 4"/><path d="M66 2c-4 6-6 9-6 12a6 6 0 0 0 12 0c0-3-2-6-6-12z"/></svg>
    <h3>Hygiene &amp; Cleanings</h3>
    <p>Thorough, professional cleanings<br>to protect your oral health.</p>
    <div class="btn">Learn More</div>
  </div>

  <div class="card" style="left:87px;top:675px">
    <svg width="70" height="76" viewBox="0 0 70 76" fill="none" stroke="#2f6e57" stroke-width="3" stroke-linecap="round" stroke-linejoin="round"><path d="M35 4l26 10v20c0 18-12 30-26 38C21 64 9 52 9 34V14z"/><path d="M30 24h10v8h8v10h-8v8H30v-8h-8V32h8z"/></svg>
    <h3>Emergency Services</h3>
    <p>Prompt, compassionate care<br>when dental issues can’t wait.</p>
    <div class="btn">Learn More</div>
  </div>
  <div class="card" style="left:436px;top:675px">
    <svg width="70" height="76" viewBox="0 0 70 76" fill="none" stroke="#2f6e57" stroke-width="3" stroke-linecap="round" stroke-linejoin="round"><path d="M20 6c-10 0-14 8-12 18 2 10 6 14 6 26 0 12 4 22 9 22 6 0 5-18 12-24 7 6 6 24 12 24 5 0 9-10 9-22 0-12 4-16 6-26 2-10-2-18-12-18-6 0-10 4-15 4S26 6 20 6z"/><path d="M22 14c5 0 9 3 13 3"/></svg>
    <h3>Restorations</h3>
    <p>Repair and strengthen teeth<br>with expertly crafted solutions.</p>
    <div class="btn">Learn More</div>
  </div>
  <div class="card" style="left:785px;top:675px">
    <svg width="80" height="60" viewBox="0 0 80 60" fill="none" stroke="#2f6e57" stroke-width="3" stroke-linecap="round" stroke-linejoin="round" style="left:124px;top:50px"><path d="M4 14c10 6 24 8 36 8s26-2 36-8c0 14-14 26-36 26S4 28 4 14z"/><path d="M16 20v10M28 22v14M40 22v16M52 22v14M64 20v10"/></svg>
    <h3>Dentures &amp; Partials</h3>
    <p>Custom full or partial dentures<br>designed for comfort and fit.</p>
    <div class="btn">Learn More</div>
  </div>
</section>

<section class="cta">
  <h2>Ready for a Healthier Smile?</h2>
  <div class="outline">Start Your Smile Journey</div>
</section>

<section class="hours">
  <div class="photo" role="img" aria-label="Photo of a patient receiving a dental check-up"></div>
  <h2 style="top:76px">Office Hours</h2>
  <div class="row" style="top:160px">Monday - Friday<span>8:00 AM - 5:00 PM</span></div>
  <div class="row" style="top:202px">Saturday<span>9:00 AM - 2:00 PM</span></div>
  <div class="row" style="top:244px">Sunday<span>Closed</span></div>
  <h2 style="top:317px">Location</h2>
  <div class="addr">48 Alder Lane<br>Brookvale, IL 62790</div>
  <div class="btn" style="left:633px;top:495px;width:185px;height:47px">Get Directions</div>
</section>

<section class="reviews">
  <h2 class="section-title" style="top:110px">What Our Patients Are Saying</h2>
  <div class="review" style="left:143px">
    <div class="stars">★★★★★</div>
    <p>“The staff is very friendly<br>and professional. Highly<br>recommend this office!”</p>
    <div class="name">Nora P</div>
  </div>
  <div class="review" style="left:457px">
    <div class="stars">★★★★★</div>
    <p>“My experience with the<br>Doctor was fantastic.<br>I feel confident in my smile!”</p>
    <div class="name">Owen T</div>
  </div>
  <div class="review" style="left:773px">
    <div class="stars">★★★★★</div>
    <p>“I had an emergency and<br>Got same-day treatment.<br>So grateful for the care!”</p>
    <div class="name">Lena D</div>
  </div>
</section>

<section class="book">
  <h2>Book an Appointment</h2>
  <p>Whether you’re a new or returning patient,<br>our friendly team is ready to provide the<br>personalized, gentle care you deserve.<br>Experience the difference at<br>Harrowfield Dentistry — where<br>comfort meets excellence.</p>
  <div class="btn" style="left:91px;top:410px;width:188px;height:49px">Schedule Now</div>
  <div class="photo" role="img" aria-label="Photo of a smiling family of four outdoors"></div>
</section>

<section class="news">
  <h2>Newsletter</h2>
  <p>Join the Harrowfield Dentistry newsletter<br>for the latest updates from our team.</p>
  <div class="field">Enter your email address</div>
  <div class="btn">Subscribe</div>
</section>

<footer class="site-footer">
  <div class="brand"><span class="dot"></span>Harrowfield Dentistry</div>
  <div class="social" aria-label="Social media links"><span></span><span></span><span></span></div>
  <div class="legal">Privacy Policy | Terms</div>
  <div class="col" style="left:518px">
    <h4>Contact</h4>
    48 Alder Lane<br>Brookvale, IL 62790<br>(555) 284-9106<br>&nbsp;info@harrowfielddentistry.com
  </div>
  <div class="col" style="left:1015px">
    <h4>Sitemap</h4>
    Home<br>Services<br>About<br>Contact
  </div>
</footer>
<div class="copy">© 2025 Harrowfield Dentistry. All rights reserved.</div>

</body>
</html>
```